Body Wash & Shampoo Label Design

Hello everyone,

I need a new logo/label design for a sister line of products to our main line. The Brand name is Velmora Trailside.

Here’s some insight to provide some inspiration. This brand will be social media based and will focus on adventure, travel, hiking, camping, and all other outdoors activities. Target market is outdoorsman – women. We will also be allocating a percentage of sales to various conservation efforts which we are narrowing down as we speak.

I’m not exactly sure what we are looking for in a logo/label designs so we are open to ideas and promote creativity. That said, we are looking for a simple and clean design that also speaks to our target market and would like the logo & label to be done at the same time so they compliment each other and fit well together.

Please incorporate an accent color somewhere in the design so new fragrances can be added down the line. This label will be going on a 16 fl oz cylindrical bottle with a toggle cap.

Label Details:

Width: 7.4 in
Height: 5.5 in
Distance from center of front to center of back: 3.7 in

Front (left):
- Logo
- Product Name: Driftwell Shampoo & Body Cleanser
- Highlights:
o No Rinse Nourishing Formula
o Sooths & Conditions
o Non-Sensitizing
o Non-Allergenic
- 16 Fl. Oz.

Back (right):

Tagline: More Cleanse, Less Hassle

Directions: Moisten wash cloth with Driftwell Shampoo & body cleanser. Use wash cloth to gently cleanse desired area. Pat dry if necessary. When shampooing, use was cloth to gently massage hair and scalp. Let air dry.

Warning: For external use only. Rinse eyes with water if contact should occur. Discontinue use in the case of local irritation. Contact physician if irritation persists for extended period of time.

Ingredients: Water, Disodium Cocoamphodiactate, Sodium C14-16 Olefine Sulfonate, ppg-2 hydroxyethyl Cocamide, Styrene/Acrylates Copolymer, Solvarin IV, Acrylates/C10-30 Alkyl Acrylate Crosspolymer, Fragrance, Aloe Barbadeniss Leaf Juice

Made in USA (either logo or words)

Address:
Quillan Products
214 Ashcombe Ln
Dover, NJ 07899

Barcode is also attached below. Looking forward to seeing your designs and thanks for the help! Let me know if you have any questions.

- Merle

Target Market(s)

Outdoorsman/women

Logo Text

Velmora Trailside

Colors

Designer to choose colors to be used in the design.

```html
<!DOCTYPE html>
<html lang="en">
<head>
<meta charset="utf-8">
<title>Driftwell Shampoo &amp; Body Cleanser – Front Label</title>
<link rel="stylesheet" href="https://fonts.googleapis.com/css2?family=Marcellus&family=Open+Sans:ital,wght@0,600;0,700;1,400;1,600&display=swap">
<style>
  :root {
    --backdrop: #f4f4f4;
    --label-top: #b9e0ea;
    --label-mid: #dff1f6;
    --label-bottom: #ffffff;
    --navy: #1d5a78;
    --accent: #5bbcd9;
    --gold: #c3902f;
    --gold-light: #e6c27a;
    --ink: #1c1c1c;
    --swirl-deep: #2e9fcb;
    --swirl-soft: #cfeaf3;
  }
  * { box-sizing: border-box; margin: 0; padding: 0; }
  html, body { width: 1200px; height: 900px; overflow: hidden; }
  body {
    background: var(--backdrop);
    font-family: "Open Sans", sans-serif;
    display: flex;
    align-items: center;
    justify-content: center;
  }
  .label-front {
    position: relative;
    width: 380px;
    height: 720px;
    background: linear-gradient(180deg, var(--label-top) 0%, var(--label-mid) 38%, var(--label-bottom) 62%, var(--label-bottom) 100%);
  }
  .brand {
    position: absolute;
    top: 150px;
    left: 0;
    right: 0;
    display: flex;
    align-items: center;
    justify-content: center;
    gap: 10px;
  }
  .brand-square {
    width: 30px;
    height: 30px;
    background: linear-gradient(135deg, var(--gold-light), var(--gold));
  }
  .brand-name {
    font-weight: 700;
    font-size: 21px;
    letter-spacing: 1px;
    text-transform: uppercase;
    color: var(--navy);
  }
  .product-title {
    position: absolute;
    top: 218px;
    left: 58px;
    font-family: "Marcellus", serif;
    font-size: 66px;
    line-height: 1;
    color: var(--navy);
  }
  .product-sub {
    position: absolute;
    top: 300px;
    left: 60px;
    font-style: italic;
    font-weight: 600;
    font-size: 15px;
    line-height: 1.25;
    color: var(--ink);
  }
  .product-badge {
    position: absolute;
    top: 282px;
    left: 200px;
    width: 132px;
    height: 58px;
    border-radius: 50%;
    background: var(--accent);
    color: #ffffff;
    font-family: "Marcellus", serif;
    font-size: 38px;
    display: flex;
    align-items: center;
    justify-content: center;
  }
  .swirl-art {
    position: absolute;
    top: 360px;
    left: 40px;
    width: 240px;
    height: 180px;
    border-radius: 50%;
    background: radial-gradient(ellipse at 45% 55%, var(--swirl-deep) 0%, var(--accent) 22%, var(--swirl-soft) 55%, rgba(255,255,255,0) 75%);
  }
  .highlights {
    position: absolute;
    top: 530px;
    left: 198px;
    list-style: none;
    font-style: italic;
    font-size: 10.5px;
    line-height: 1.45;
    color: var(--ink);
  }
  .volume {
    position: absolute;
    top: 618px;
    left: 198px;
    font-family: "Marcellus", serif;
    font-weight: 700;
    font-size: 20px;
    color: var(--ink);
  }
</style>
</head>
<body>
  <main class="label-front">
    <div class="brand">
      <span class="brand-square"></span>
      <span class="brand-name">Velmora Trailside</span>
    </div>
    <h1 class="product-title">Drift</h1>
    <span class="product-badge">well</span>
    <p class="product-sub">Shampoo &amp;<br>Body Cleanser</p>
    <div class="swirl-art" role="img" aria-label="Soft flowing blue ribbon swirl artwork"></div>
    <ul class="highlights">
      <li>No Rinse Nourishing Formula</li>
      <li>Sooths &amp; Conditions</li>
      <li>Non-Sensitizing</li>
      <li>Non-Allergenic</li>
    </ul>
    <p class="volume">16 Fl. Oz</p>
  </main>
</body>
</html>
```